Verlindo Magician

I want the business card for my business to give to people who watch that later I will be employed to show magic here is my website http://www.balsamomagicien.com/I want the interesting design , i am very opened for formal and informal, I watch a lot of design so don't stick to the common shape and form but i hope it can also be produced the thing to write on will be the same as in picture that i will upload , i also will upload the logo for you that so can be easy to useDenis CostilleMagicianMAGICIAN VERLINDO 17 rue des Tilleuls - 25000 BESANÇON contact@verlindoillusions.example tel. 0381 946 157 tel. 0674 219 503

```html
<!DOCTYPE html>
<html lang="en">
<head>
<meta charset="utf-8">
<title>Verlindo Magician – Business Card</title>
<link rel="stylesheet" href="https://fonts.googleapis.com/css2?family=Montserrat:wght@300;400;500&display=swap">
<style>
  :root {
    --backdrop: #2a2c30;
    --card: #ffffff;
    --ink: #111111;
    --ink-soft: #555555;
    --suit-red: #e0141b;
    --figure-dark: #0b0b0b;
    --figure-mid: #2a2a2a;
    --rule: #222222;
  }
  * { box-sizing: border-box; margin: 0; padding: 0; }
  html, body {
    width: 1200px; height: 900px; overflow: hidden;
    background: var(--backdrop);
    font-family: "Montserrat", Arial, sans-serif;
    color: var(--ink);
  }
  .canvas { position: relative; width: 1200px; height: 900px; }

  /* Front: contact side */
  .card-front {
    position: absolute; left: 50px; top: 280px;
    width: 620px; height: 354px;
    background: var(--card); border-radius: 26px;
  }
  .brand {
    position: absolute; left: 36px; top: 30px;
    display: flex; flex-direction: column; align-items: center; width: 170px;
  }
  .brand-figure {
    width: 110px; height: 110px; border-radius: 6px;
    background: linear-gradient(160deg, var(--figure-mid), var(--figure-dark));
  }
  .brand-name {
    margin-top: 8px; font-size: 15px; font-weight: 300; letter-spacing: 1px;
    text-transform: uppercase; white-space: nowrap; color: var(--ink);
  }
  .identity {
    position: absolute; right: 40px; top: 96px; text-align: right;
  }
  .person-name {
    font-size: 31px; font-weight: 400; letter-spacing: 1px; text-transform: uppercase;
  }
  .person-role {
    font-size: 14px; font-weight: 300; letter-spacing: 1.5px; color: var(--ink-soft);
    text-transform: uppercase; margin-top: 2px;
  }
  .address {
    position: absolute; right: 118px; top: 186px;
    display: flex; align-items: flex-start; gap: 12px;
  }
  .address-lines {
    font-size: 19px; font-weight: 400; line-height: 1.05; text-transform: uppercase; letter-spacing: .5px;
  }
  .icon { width: 20px; height: 20px; flex: none; }
  .address .icon { width: 22px; height: 26px; margin-top: 2px; }
  .contacts {
    position: absolute; right: 40px; bottom: 34px;
    list-style: none; text-align: right;
  }
  .contacts li {
    display: flex; justify-content: flex-end; align-items: center; gap: 12px;
    font-size: 12.5px; font-weight: 300; letter-spacing: .6px; text-transform: uppercase;
    line-height: 1.75;
  }
  .contacts .icon { width: 15px; height: 15px; }

  /* Back: playing card side */
  .card-back {
    position: absolute; left: 740px; top: 186px;
    width: 380px; height: 532px;
    background: var(--card); border-radius: 26px;
  }
  .card-frame {
    position: absolute; inset: 26px 30px; border: 1.5px solid var(--rule);
  }
  .side-label {
    position: absolute; font-size: 18px; font-weight: 400; letter-spacing: 3px;
    text-transform: uppercase; white-space: nowrap; line-height: 1;
    writing-mode: vertical-rl;
  }
  .side-label.left { left: 40px; top: 58px; }
  .side-label.right { right: 40px; bottom: 58px; transform: rotate(180deg); }
  .suit { position: absolute; width: 36px; height: 36px; }
  .suit.spade { left: 150px; top: 38px; width: 40px; height: 40px; }
  .suit.diamond { left: 70px; top: 118px; }
  .suit.heart { right: 70px; bottom: 118px; }
  .suit.club { right: 150px; bottom: 38px; width: 40px; height: 40px; }
  .court-figure {
    position: absolute; left: 114px; top: 84px; width: 152px; height: 364px;
    border-radius: 36px;
    background: linear-gradient(150deg, var(--figure-mid), var(--figure-dark) 45%, var(--figure-mid) 55%, var(--figure-dark));
  }
</style>
</head>
<body>
<main class="canvas">

  <section class="card-front" aria-label="Business card, contact side">
    <div class="brand">
      <div class="brand-figure" role="img" aria-label="Black ink portrait of the magician holding playing cards"></div>
      <span class="brand-name">Verlindo Magician</span>
    </div>

    <header class="identity">
      <h1 class="person-name">Marc Ravoulet</h1>
      <p class="person-role">Magician</p>
    </header>

    <div class="address">
      <svg class="icon" viewBox="0 0 22 26" aria-hidden="true">
        <path d="M11 1a8 8 0 0 0-8 8c0 6 8 13 8 13s8-7 8-13a8 8 0 0 0-8-8z" fill="var(--ink)"/>
        <circle cx="11" cy="9" r="3" fill="var(--card)"/>
        <ellipse cx="11" cy="23.5" rx="7" ry="1.8" fill="none" stroke="var(--ink)" stroke-width="1.5"/>
      </svg>
      <p class="address-lines">17 rue des Tilleuls<br>25000 Besançon</p>
    </div>

    <ul class="contacts">
      <li>contact@verlindoillusions.example
        <svg class="icon" viewBox="0 0 16 16" aria-hidden="true"><rect x="1" y="3" width="14" height="10" fill="var(--ink)"/><path d="M1 3l7 6 7-6" fill="none" stroke="var(--card)" stroke-width="1.3"/></svg>
      </li>
      <li>0381 946 157/0674 219 503
        <svg class="icon" viewBox="0 0 16 16" aria-hidden="true"><path d="M4 1l3 3-2 2c1 2 3 4 5 5l2-2 3 3-2 3C7 15 1 9 1 3z" fill="var(--ink)"/></svg>
      </li>
      <li>www.verlindoillusions.example
        <svg class="icon" viewBox="0 0 16 16" aria-hidden="true"><circle cx="8" cy="8" r="7" fill="var(--ink)"/><path d="M1 8h14M8 1c-3 3-3 11 0 14M8 1c3 3 3 11 0 14M2.5 4.5h11M2.5 11.5h11" fill="none" stroke="var(--card)" stroke-width=".9"/></svg>
      </li>
    </ul>
  </section>

  <section class="card-back" aria-label="Business card, playing card side">
    <div class="card-frame"></div>
    <span class="side-label left">Verlindo</span>
    <span class="side-label right">Verlindo</span>

    <svg class="suit spade" viewBox="0 0 40 40" aria-hidden="true">
      <path d="M20 3C14 12 5 17 5 24a7 7 0 0 0 13 3c-1 5-3 8-6 10h16c-3-2-5-5-6-10a7 7 0 0 0 13-3c0-7-9-12-15-21z" fill="var(--ink)"/>
    </svg>
    <svg class="suit diamond" viewBox="0 0 40 40" aria-hidden="true">
      <path d="M20 2l14 18-14 18L6 20z" fill="var(--suit-red)"/>
    </svg>

    <div class="court-figure" role="img" aria-label="Mirrored black ink illustration of the magician holding cards, as on a court card"></div>

    <svg class="suit heart" viewBox="0 0 40 40" aria-hidden="true">
      <path d="M20 37C8 27 2 20 2 12a9 9 0 0 1 18-2 9 9 0 0 1 18 2c0 8-6 15-18 25z" fill="var(--suit-red)"/>
    </svg>
    <svg class="suit club" viewBox="0 0 40 40" aria-hidden="true">
      <circle cx="20" cy="11" r="8" fill="var(--ink)"/>
      <circle cx="10" cy="23" r="8" fill="var(--ink)"/>
      <circle cx="30" cy="23" r="8" fill="var(--ink)"/>
      <path d="M18 20h4c0 8 2 13 6 17H12c4-4 6-9 6-17z" fill="var(--ink)"/>
    </svg>
  </section>

</main>
</body>
</html>
```